Salon and Spa Distributor Business Card

Need a business card. We are are distributor in the salon and spa industry. We identify with natural beauty. Need a card with:
Company Name: Petal Quarry"
Title: "President & CEO"
Address
Company Phone number
email
website
Tag Line:" The Professional Salon Source"

Industry/Entity Type

Business

Contact Information for Business Card

Name: Dov Strommen
Title: "President & CEO"
Address: 31 Harlow Ln, Bexmoor, NJ 07813
Company Phone number: 800-463-5918
email: dovstrommen@petalquarry.example
website: www.petalquarry.example

Requirements
Should not have
• No black backgrounds

```html
<!DOCTYPE html>
<html lang="en">
<head>
<meta charset="utf-8">
<title>Petal Quarry — Business Card</title>
<link rel="stylesheet" href="https://fonts.googleapis.com/css2?family=Questrial&family=Tinos:ital@1&display=swap">
<style>
  :root {
    --page-bg: #ececec;
    --brand-green: #52a641;
    --brand-green-dark: #0f6b35;
    --brand-green-light: #6cbf45;
    --card-white: #f7f7f7;
    --ink: #1d1d1d;
    --white: #ffffff;
  }
  * { margin: 0; padding: 0; box-sizing: border-box; }
  html, body { width: 1200px; height: 586px; overflow: hidden; }
  body {
    background: var(--page-bg);
    position: relative;
    font-family: "Questrial", "Century Gothic", sans-serif;
  }
  .card {
    position: absolute;
    top: 129px;
    width: 502px;
    height: 301px;
    overflow: hidden;
  }

  /* Front */
  .card-front { left: 61px; background: var(--brand-green); color: var(--white); }
  .front-brand {
    position: absolute;
    top: 62px; left: 0; right: 0;
    display: flex; align-items: center; justify-content: center; gap: 14px;
  }
  .front-brand .brand-dot {
    width: 30px; height: 30px; border-radius: 50%; background: var(--white);
  }
  .front-brand .brand-name { font-size: 42px; color: var(--white); }
  .front-web {
    position: absolute; top: 239px; left: 0; right: 0;
    display: flex; align-items: center; justify-content: center; gap: 6px;
    font-size: 13px; letter-spacing: 0.02em;
  }
  .front-web .rule { width: 58px; height: 2px; background: var(--white); }
  .front-tagline {
    position: absolute; top: 263px; left: 0; right: 0; text-align: center;
    font-family: "Tinos", "Times New Roman", serif; font-style: italic;
    font-size: 12.5px; letter-spacing: 0.36em;
  }

  /* Back */
  .card-back { left: 619px; background: var(--card-white); color: var(--ink); }
  .back-brand {
    position: absolute; top: 54px; right: 24px;
    display: flex; align-items: center; gap: 12px;
  }
  .back-brand .brand-dot {
    width: 34px; height: 34px; border-radius: 50%; background: var(--brand-green);
  }
  .back-brand .brand-name { font-size: 26px; color: var(--brand-green); }
  .person-name {
    position: absolute; top: 138px; left: 29px;
    font-size: 17px; color: var(--brand-green);
  }
  .person-title {
    position: absolute; top: 162px; left: 29px;
    font-family: "Tinos", "Times New Roman", serif; font-style: italic; font-size: 11.5px;
  }
  .contact-list { position: absolute; top: 202px; left: 29px; list-style: none; }
  .contact-item {
    display: flex; align-items: center; gap: 7px;
    height: 18px; margin-bottom: 6px; font-size: 12px;
  }
  .contact-icon { width: 18px; height: 18px; flex: none; }
  .accent-band {
    position: absolute; left: 0; right: 0; bottom: 0; height: 13px;
    background: linear-gradient(90deg, var(--brand-green-dark), var(--brand-green-light) 50%, var(--brand-green-dark));
  }
</style>
</head>
<body>
  <section class="card card-front">
    <div class="front-brand">
      <span class="brand-dot"></span>
      <span class="brand-name">Petal Quarry</span>
    </div>
    <div class="front-web"><span class="rule"></span>www.petalquarry.example<span class="rule"></span></div>
    <p class="front-tagline">The Professional Salon Source</p>
  </section>

  <section class="card card-back">
    <div class="back-brand">
      <span class="brand-dot"></span>
      <span class="brand-name">Petal Quarry</span>
    </div>
    <h1 class="person-name">Dov Strommen</h1>
    <p class="person-title">President &amp; CEO</p>
    <ul class="contact-list">
      <li class="contact-item">
        <svg class="contact-icon" viewBox="0 0 18 18" aria-hidden="true">
          <circle cx="9" cy="9" r="9" fill="#52a641"/>
          <path d="M5 7.5c0-1.5 2-2.3 4-2.3s4 .8 4 2.3l-1.6.3-.4-1.2H7l-.4 1.2z M6.3 8.5h5.4l.8 4H5.5z" fill="#fff"/>
        </svg>800-463-5918
      </li>
      <li class="contact-item">
        <svg class="contact-icon" viewBox="0 0 18 18" aria-hidden="true">
          <circle cx="9" cy="9" r="9" fill="#52a641"/>
          <rect x="4.5" y="6" width="9" height="6.5" fill="none" stroke="#fff" stroke-width="1.2"/>
          <path d="M4.5 6l4.5 3.8L13.5 6" fill="none" stroke="#fff" stroke-width="1.2"/>
        </svg>dovstrommen@petalquarry.example
      </li>
      <li class="contact-item">
        <svg class="contact-icon" viewBox="0 0 18 18" aria-hidden="true">
          <circle cx="9" cy="9" r="9" fill="#52a641"/>
          <path d="M9 3.8a3.6 3.6 0 0 1 3.6 3.6C12.6 10 9 14.2 9 14.2S5.4 10 5.4 7.4A3.6 3.6 0 0 1 9 3.8z" fill="#fff"/>
          <circle cx="9" cy="7.4" r="1.4" fill="#52a641"/>
        </svg>31 Harlow Ln, Bexmoor, NJ 07813
      </li>
    </ul>
    <div class="accent-band"></div>
  </section>
</body>
</html>
```